RWT Fittings Ltd Business Cards

We need a business card with our business logo. We provide window and door installations on high-rises in west coast British Colombia, Canada.

I would like my business information and details on one side of the card, and the other side the company name with logo

Target Market(s)

General Contractors

Industry/Entity Type

Construction

Contact Information for Business Card

one side i want my company name and logo in the dark theme logo that i provided

Requirements
Must have
• Marco Peltieri, 16045518293, RWTFittings@mailbox-demo.com, 1407-5194 Linden Row Burnaby BC, V5H 2K9, Owner & Manager

```html
<!DOCTYPE html>
<html lang="en">
<head>
<meta charset="utf-8">
<title>RWT Fittings Ltd – Business Cards</title>
<link href="https://fonts.googleapis.com/css2?family=Roboto:wght@400;500;700&display=swap" rel="stylesheet">
<style>
  :root {
    --page-bg: #222222;
    --card-white: #ffffff;
    --brand-blue: #29abe2;
    --brand-grey: #9a9a9a;
    --ink: #1e1e1e;
    --dark-top: #1c1a18;
    --dark-mid: #3a3632;
    --dark-low: #4a4540;
  }
  * { margin: 0; padding: 0; box-sizing: border-box; }
  html, body {
    width: 1200px; height: 780px; overflow: hidden;
    background: var(--page-bg);
    font-family: "Roboto", Arial, sans-serif;
  }
  .sheet {
    position: relative; width: 1200px; height: 780px;
    display: flex; align-items: center; justify-content: center; gap: 40px;
  }
  .card {
    position: relative; width: 540px; height: 308px; overflow: hidden;
    box-shadow: 0 14px 30px rgba(0,0,0,.45);
  }

  /* Front: contact side */
  .card-front { background: var(--card-white); }
  .front-brand {
    position: absolute; left: 34px; top: 92px; width: 210px;
    display: flex; align-items: center; gap: 10px;
  }
  .brand-square { width: 18px; height: 18px; background: var(--brand-grey); flex: none; }
  .brand-name {
    font-weight: 700; font-size: 23px; line-height: 1.1; color: var(--brand-blue);
  }
  .divider {
    position: absolute; left: 268px; top: 48px; width: 1px; height: 170px; background: var(--ink);
  }
  .contact { position: absolute; left: 292px; top: 74px; }
  .person-name { font-weight: 700; font-size: 27px; letter-spacing: .2px; }
  .person-name .first { color: var(--brand-blue); }
  .person-name .last { color: var(--brand-grey); }
  .person-role { font-weight: 500; font-size: 13px; color: var(--ink); margin-top: 2px; }
  .contact-list { list-style: none; margin-top: 14px; }
  .contact-list li {
    display: flex; align-items: center; gap: 8px;
    font-size: 13px; color: var(--ink); margin-bottom: 6px;
  }
  .contact-list svg { width: 13px; height: 13px; flex: none; }
  .address-band {
    position: absolute; left: 0; bottom: 20px; width: 430px; height: 30px;
    background: var(--brand-blue); color: var(--card-white);
    font-size: 13px; display: flex; align-items: center; padding-left: 56px;
  }
  .corner-mark {
    position: absolute; right: 34px; bottom: 18px; width: 34px; height: 34px;
    background: var(--brand-blue);
  }
  .corner-block {
    position: absolute; right: 0; bottom: 0; width: 34px; height: 26px; background: var(--brand-grey);
  }

  /* Back: brand side */
  .card-back { background: var(--dark-top); }
  .back-photo {
    position: absolute; inset: 0;
    background:
      radial-gradient(ellipse at 75% 70%, var(--dark-low) 0%, transparent 60%),
      linear-gradient(160deg, var(--dark-top) 0%, var(--dark-mid) 60%, var(--dark-low) 100%);
  }
  .back-brand {
    position: absolute; inset: 0;
    display: flex; align-items: center; justify-content: center; gap: 12px;
  }
  .back-brand .brand-square { width: 22px; height: 22px; }
  .back-brand .brand-name { font-size: 34px; }
</style>
</head>
<body>
<main class="sheet">

  <section class="card card-front" aria-label="Business card, contact side">
    <div class="front-brand">
      <span class="brand-square"></span>
      <span class="brand-name">RWT Fittings Ltd</span>
    </div>

    <div class="divider"></div>

    <div class="contact">
      <h1 class="person-name"><span class="first">Marco</span> <span class="last">Peltieri</span></h1>
      <p class="person-role">Owner &amp; Manager</p>
      <ul class="contact-list">
        <li>
          <svg viewBox="0 0 24 24" aria-hidden="true"><path fill="#29abe2" d="M6.6 10.8a15.1 15.1 0 0 0 6.6 6.6l2.2-2.2a1 1 0 0 1 1-.25 11.4 11.4 0 0 0 3.6.57 1 1 0 0 1 1 1V20a1 1 0 0 1-1 1A17 17 0 0 1 3 4a1 1 0 0 1 1-1h3.5a1 1 0 0 1 1 1c0 1.25.2 2.45.57 3.6a1 1 0 0 1-.25 1z"/></svg>
          1604 551 8293
        </li>
        <li>
          <svg viewBox="0 0 24 24" aria-hidden="true"><rect x="2" y="5" width="20" height="14" rx="2" fill="#29abe2"/><path d="M3 6l9 7 9-7" fill="none" stroke="#fff" stroke-width="1.8"/></svg>
          RWTFittings@mailbox-demo.com
        </li>
      </ul>
    </div>

    <div class="address-band">1407-5194 Linden Row Burnaby BC, V5H 2K9</div>
    <div class="corner-mark"></div>
    <div class="corner-block"></div>
  </section>

  <section class="card card-back" aria-label="Business card, brand side">
    <div class="back-photo" role="img" aria-label="Softly blurred dark photograph of a modern interior"></div>
    <div class="back-brand">
      <span class="brand-square"></span>
      <span class="brand-name">RWT Fittings Ltd</span>
    </div>
  </section>

</main>
</body>
</html>
```